Weightloss company needs Business Card

We want a business card that is clean and professional, yet portrays that we are a friendly, innovative, and versatile program designed to fit the needs of our clients.
I would like there to be 2 sides, one side having an appointment card, and the other side containing the logo and business information. There can be decorations on both sides. The logo is attached.

Target Market(s)

Men and women 40-60

Industry/Entity Type

Business

Contact Information for Business Card

Font styles to use
Sans Serif

Requirements
Must have
• The logo, space for business information
Nice to have
• The colors in the logo
Should not have
• No pictures of people or food

```html
<!DOCTYPE html>
<html lang="en">
<head>
<meta charset="UTF-8">
<title>Risewell Weightloss – Business Card</title>
<link rel="stylesheet" href="https://fonts.googleapis.com/css2?family=Open+Sans:ital,wght@0,400;0,600;0,700;1,400&display=swap">
<style>
  :root {
    --brand-red: #d5002b;
    --brand-blue: #2bb6e0;
    --ink: #555759;
    --ink-soft: #6b6d70;
    --dots: #8a8c8f;
    --card: #f4f4f4;
    --backdrop: #9a9c9c;
    --divider: #a7a9ab;
  }
  * { box-sizing: border-box; margin: 0; padding: 0; }
  html, body {
    width: 1105px; height: 1200px; overflow: hidden;
    background: var(--backdrop);
    font-family: "Open Sans", sans-serif;
  }
  .card {
    position: absolute; left: 182px; width: 748px; height: 427px;
    background: var(--card); overflow: hidden;
  }
  .card--front { top: 119px; }
  .card--back { top: 635px; }

  /* Front */
  .brand {
    position: absolute; left: 70px; top: 160px; width: 300px;
    display: flex; align-items: center; gap: 12px;
    color: var(--brand-red); font-weight: 700; font-size: 32px; line-height: 1.05;
  }
  .brand__dot {
    width: 22px; height: 22px; border-radius: 50%; background: var(--brand-blue); flex: none;
  }
  .divider {
    position: absolute; left: 395px; top: 75px; width: 2px; height: 241px; background: var(--divider);
  }
  .contact { position: absolute; left: 432px; top: 66px; }
  .contact__name { color: var(--brand-red); font-size: 27px; font-weight: 600; line-height: 36px; }
  .contact__role { color: var(--brand-blue); font-size: 20px; line-height: 26px; margin-bottom: 14px; }
  .contact__address { color: var(--ink); font-size: 20px; line-height: 27px; margin-bottom: 6px; }
  .contact__line {
    display: flex; align-items: center; gap: 12px;
    color: var(--ink); font-size: 20px; line-height: 29px;
  }
  .contact__line svg { width: 18px; height: 18px; fill: var(--brand-red); flex: none; }

  .footer-stripe {
    position: absolute; left: 0; bottom: 44px; width: 100%; height: 6px; background: var(--brand-blue);
  }
  .footer-band {
    position: absolute; left: 0; bottom: 0; width: 100%; height: 40px; background: var(--brand-red);
    display: flex; align-items: center; justify-content: flex-end; padding-right: 40px;
  }
  .website { color: #fff; font-size: 18px; font-weight: 600; letter-spacing: 1px; }

  /* Back */
  .appt__title {
    position: absolute; top: 36px; width: 100%; text-align: center;
    color: var(--brand-red); font-size: 27px; font-weight: 600;
  }
  .field {
    position: absolute; display: flex; align-items: flex-end;
    color: var(--brand-red); font-size: 19px;
  }
  .field__dots { flex: 1; border-bottom: 2px dotted var(--dots); margin: 0 0 6px 8px; height: 2px; }
  .field--name { left: 43px; top: 104px; width: 647px; }
  .field--date { left: 39px; top: 157px; width: 355px; }
  .field--time { left: 417px; top: 157px; width: 205px; }
  .ampm { position: absolute; left: 633px; top: 163px; color: var(--brand-red); font-size: 15px; }
  .field--note { left: 44px; top: 263px; width: 646px; }
  .line-blank { position: absolute; left: 44px; top: 320px; width: 646px; border-bottom: 2px dotted var(--dots); }
  .day {
    position: absolute; top: 219px; display: flex; align-items: center; gap: 8px;
    color: var(--brand-red); font-size: 18px;
  }
  .day__box { width: 21px; height: 19px; border: 1.5px solid var(--ink); background: #fff; }
  .policy {
    position: absolute; top: 357px; width: 100%; text-align: center;
    color: var(--ink-soft); font-size: 15px; font-style: italic; line-height: 21px;
  }
</style>
</head>
<body>

<section class="card card--front">
  <div class="brand"><span class="brand__dot"></span><span>Risewell<br>Weightloss</span></div>
  <div class="divider"></div>
  <div class="contact">
    <div class="contact__name">DANIEL HARPER</div>
    <div class="contact__role">CEO/FOUNDER</div>
    <div class="contact__address">1420 Birchwood Road<br>Fairview, Alaska 99501</div>
    <div class="contact__line">
      <svg viewBox="0 0 24 24"><path d="M6.6 10.8a15 15 0 0 0 6.6 6.6l2.2-2.2a1 1 0 0 1 1-.25 11.4 11.4 0 0 0 3.6.57 1 1 0 0 1 1 1V20a1 1 0 0 1-1 1A17 17 0 0 1 3 4a1 1 0 0 1 1-1h3.5a1 1 0 0 1 1 1c0 1.250.2 2.45.57 3.57a1 1 0 0 1-.25 1z"/></svg>
      <span>555 210 4417</span>
    </div>
    <div class="contact__line">
      <svg viewBox="0 0 24 24"><path d="M7 1h10a2 2 0 0 1 2 2v18a2 2 0 0 1-2 2H7a2 2 0 0 1-2-2V3a2 2 0 0 1 2-2zm0 3v14h10V4zm5 15.5a1.2 1.2 0 1 0 0 2.4 1.2 1.2 0 0 0 0-2.4z"/></svg>
      <span>555 382 7605</span>
    </div>
    <div class="contact__line">
      <svg viewBox="0 0 24 24"><path d="M6 2h12v6H6zM3 9h18a2 2 0 0 1 2 2v7h-4v4H5v-4H1v-7a2 2 0 0 1 2-2zm4 7v4h10v-4z"/></svg>
      <span>555 624 3098</span>
    </div>
    <div class="contact__line">
      <svg viewBox="0 0 24 24"><path d="M2 5h20v14H2zm2 2v.5l8 5 8-5V7zm0 2.8V17h16V9.8l-8 5z"/></svg>
      <span>hello@risewellfit.com</span>
    </div>
  </div>
  <div class="footer-stripe"></div>
  <div class="footer-band"><span class="website">www.risewellfit.com</span></div>
</section>

<section class="card card--back">
  <h2 class="appt__title">Next Appointment</h2>
  <div class="field field--name"><span>Name :</span><span class="field__dots"></span></div>
  <div class="field field--date"><span>Date :</span><span class="field__dots"></span></div>
  <div class="field field--time"><span>Time :</span><span class="field__dots"></span></div>
  <span class="ampm">AM/PM</span>
  <div class="day" style="left:43px">Sun <span class="day__box"></span></div>
  <div class="day" style="left:138px">Mon <span class="day__box"></span></div>
  <div class="day" style="left:239px">Tue <span class="day__box"></span></div>
  <div class="day" style="left:347px">Wed <span class="day__box"></span></div>
  <div class="day" style="left:447px">Thu <span class="day__box"></span></div>
  <div class="day" style="left:551px">Fri <span class="day__box"></span></div>
  <div class="day" style="left:630px">Sat <span class="day__box"></span></div>
  <div class="field field--note"><span>Note :</span><span class="field__dots"></span></div>
  <div class="line-blank"></div>
  <p class="policy">Please give me 24 hours notice if you are unable to keep your appointment or<br>a cancellation fee may be charged.</p>
</section>

</body>
</html>
```